Dynamic Business Card for Sports Supplements Company

Hi! I'm looking for an awesome business card to match my existing sports supplement company. I have uploaded my current company logo and screenshot of the front page of my website.

I would like to have something dynamic and interesting and utilize the colors in the website - the reds and purples

The business card should be double sided and focus on a unique eye-catching design on the back and include all the relevant company info.

Most importantly, it should say somewhere: "Sign up on our website for a coupon code."

Target Market(s)

Mostly for women gym goers but it shouldn't be too feminine. It should be in keeping with the website design. It should flow and clearly be connected to it

Industry/Entity Type

Business

Contact Information for Business Card

Lorraine K. Vestal
CEO
LVestal@Quorvanexco.com
www.quorvanexco.com
555.417.3820
P.O. Box 47315
Marlow Falls, Westmere 00000

Sign up on our website for a coupon code

Font styles to use
Serif
Sans Serif
Other font styles liked:
• Novecento font family and "Quorvanex" is in AR Destine font

Requirements
Must have
• One side should be a bold Quorvanex logo design. Even just the symbol itself may be o.k. (see attached file)

```html
<!DOCTYPE html>
<html lang="en">
<head>
<meta charset="utf-8">
<title>Quorvanex Business Card</title>
<link href="https://fonts.googleapis.com/css2?family=Open+Sans:wght@400;600;700;800&display=swap" rel="stylesheet">
<style>
  :root {
    --stage: #e9e6e1;
    --card-dark: #0d0d0d;
    --card-dark-edge: #2a2a2a;
    --brand-red: #e41e26;
    --text-light: #f2f2f2;
    --text-muted: #bdbdbd;
  }
  * { box-sizing: border-box; margin: 0; padding: 0; }
  html, body {
    width: 1200px; height: 950px; overflow: hidden;
    background: var(--stage);
    font-family: "Open Sans", Arial, sans-serif;
  }
  .card-set {
    position: relative; width: 1200px; height: 950px;
    display: flex; justify-content: center; align-items: center; gap: 80px;
  }
  .card {
    width: 400px; height: 700px; border-radius: 6px;
    position: relative; overflow: hidden;
    box-shadow: 0 18px 40px rgba(0,0,0,0.25);
  }
  .card-front {
    background: linear-gradient(160deg, var(--card-dark-edge) 0%, var(--card-dark) 45%, #000 100%);
    color: var(--text-light);
  }
  .brand-lockup {
    position: absolute; top: 150px; left: 0; right: 0;
    display: flex; flex-direction: column; align-items: center;
  }
  .brand-mark {
    width: 26px; height: 26px; background: var(--brand-red); margin-bottom: 18px;
  }
  .brand-name {
    font-weight: 800; font-size: 46px; letter-spacing: 1px;
    text-transform: uppercase; color: var(--text-light); line-height: 1;
  }
  .brand-tagline {
    margin-top: 8px; font-size: 13px; letter-spacing: 3.2px;
    text-transform: uppercase; color: var(--text-muted);
  }
  .contact-block {
    position: absolute; left: 46px; right: 30px; top: 395px;
  }
  .person-name {
    color: var(--brand-red); font-weight: 600; font-size: 25px;
    letter-spacing: 1.5px; text-transform: uppercase;
  }
  .person-title { font-size: 18px; margin: 4px 0 14px; }
  .address-line { font-size: 18px; line-height: 1.35; }
  .contact-list { list-style: none; margin-top: 6px; }
  .contact-item {
    display: flex; align-items: center; gap: 10px;
    font-size: 18px; line-height: 1.5;
  }
  .contact-icon { width: 16px; height: 16px; flex: none; }
  .card-back {
    background: var(--brand-red); color: #fff;
  }
  .back-brand {
    position: absolute; top: 290px; left: 0; right: 0;
    display: flex; flex-direction: column; align-items: center; gap: 22px;
  }
  .back-brand .brand-mark { background: #fff; width: 40px; height: 40px; margin: 0; }
  .back-brand .brand-name { color: #fff; font-size: 48px; }
  .coupon-note {
    position: absolute; bottom: 56px; left: 0; right: 0;
    text-align: center; font-size: 17px; font-weight: 600;
  }
</style>
</head>
<body>
<main class="card-set">
  <section class="card card-front" aria-label="Business card front">
    <div class="brand-lockup">
      <span class="brand-mark" aria-hidden="true"></span>
      <span class="brand-name">Quorvanex</span>
      <span class="brand-tagline">Your performance partner</span>
    </div>
    <div class="contact-block">
      <p class="person-name">Lorraine K. Vestal</p>
      <p class="person-title">CEO</p>
      <p class="address-line">P.O. Box 47315</p>
      <p class="address-line">Marlow Falls, Westmere 00000</p>
      <ul class="contact-list">
        <li class="contact-item">
          <svg class="contact-icon" viewBox="0 0 16 16" aria-hidden="true"><path fill="#e41e26" d="M3.5 1.5l2.5 0 1 3.5-1.7 1.2a9 9 0 0 0 4.5 4.5L11 9l3.5 1v2.5c0 1-1 2-2 2C6.5 14.5 1.5 9.5 1.5 3.5c0-1 1-2 2-2z"/></svg>
          555.417.3820
        </li>
        <li class="contact-item">
          <svg class="contact-icon" viewBox="0 0 16 16" aria-hidden="true"><rect x="1" y="3" width="14" height="10" rx="1.5" fill="#e41e26"/><path d="M1.5 4l6.5 5 6.5-5" stroke="#0d0d0d" stroke-width="1.3" fill="none"/></svg>
          LVestal@Quorvanexco.com
        </li>
        <li class="contact-item">
          <svg class="contact-icon" viewBox="0 0 16 16" aria-hidden="true"><circle cx="8" cy="8" r="6.5" fill="none" stroke="#e41e26" stroke-width="1.6"/><path d="M1.5 8h13M8 1.5c-3 3.5-3 9.5 0 13M8 1.5c3 3.5 3 9.5 0 13" stroke="#e41e26" stroke-width="1.2" fill="none"/></svg>
          www.quorvanexco.com
        </li>
      </ul>
    </div>
  </section>

  <section class="card card-back" aria-label="Business card back">
    <div class="back-brand">
      <span class="brand-mark" aria-hidden="true"></span>
      <span class="brand-name">Quorvanex</span>
    </div>
    <p class="coupon-note">Sign up on our website for a coupon code</p>
  </section>
</main>
</body>
</html>
```